Canadian Christian Church needs design for new sermon series

A graphic design for our series and an invitation card to invite people to the series. Check design brief for more detailed information. Target audience: young families and young adults. Looking for a creative design that will get people's attention and create interest. See design brief for copy of design purchased for previous series.
Updates
entered Apr 4 incorrectly. Need a week to receive and review designs, and today is Apr 2/19. Thanks!
Target Market(s)
young families and young adults
Colors
Designer to choose colors to be used in the design.
Look and feel

```html
<!DOCTYPE html>
<html lang="en">
<head>
<meta charset="utf-8">
<title>Messy – Sermon Series Invitation Card</title>
<link href="https://fonts.googleapis.com/css2?family=Montserrat:wght@400;600;700;800&family=Cinzel:wght@600&family=Lato:wght@400&family=Roboto+Condensed:wght@400&family=Lora:wght@500&display=swap" rel="stylesheet">
<style>
  :root{
    --page:#e0e0e0;
    --ink:#3b302b;
    --ink-deep:#1e1714;
    --sand:#c9c0ac;
    --sand-dark:#b3a88f;
    --mist:#e6e2d6;
    --white:#ffffff;
    --accent:#6a4a8c;
  }
  *{box-sizing:border-box;margin:0;padding:0}
  html,body{width:1200px;height:1200px;overflow:hidden;background:var(--page)}
  body{position:relative;font-family:"Montserrat",sans-serif}

  .card{position:absolute;left:271px;width:594px;height:468px;overflow:hidden}

  /* front */
  .card--front{top:95px}
  .front-photo{position:absolute;inset:0;
    background:
      radial-gradient(ellipse 55% 60% at 72% 42%, rgba(120,105,92,.75), rgba(120,105,92,0) 70%),
      linear-gradient(180deg,var(--mist) 0%,#d8d2c4 55%,#7a6e64 78%,var(--ink-deep) 100%);}
  .front-frame{position:absolute;left:8px;top:12px;right:8px;bottom:12px;border:2px solid var(--ink)}
  .brand{position:absolute;left:26px;top:40px;width:210px;text-align:center}
  .brand-dot{display:block;margin:0 auto 10px;width:70px;height:70px;border-radius:50%;background:var(--accent)}
  .brand-name{font-family:"Roboto Condensed",sans-serif;font-size:19px;color:var(--ink);white-space:nowrap}
  .series-title{position:absolute;left:24px;top:170px;font-weight:800;font-size:84px;line-height:1;color:var(--ink);letter-spacing:1px}
  .series-tagline{position:absolute;left:27px;top:248px;width:488px;height:50px;background:var(--ink);
    color:var(--white);font-family:"Cinzel",serif;font-weight:600;font-size:33px;line-height:50px;text-align:center;letter-spacing:.5px}
  .front-url{position:absolute;right:22px;bottom:18px;font-family:"Lora",serif;font-weight:500;font-size:17px;letter-spacing:2.5px;color:var(--white)}

  /* back */
  .card--back{top:637px;background:
      radial-gradient(ellipse 70% 50% at 15% 25%, rgba(255,255,255,.25), rgba(255,255,255,0) 70%),
      linear-gradient(180deg,var(--sand-dark) 0%,var(--sand) 60%,#c2b8a3 100%)}
  .services-title{position:absolute;left:0;right:0;top:12px;text-align:center;color:var(--white);font-weight:800;font-size:40px;line-height:1.1}
  .services-time{position:absolute;left:0;right:0;top:60px;text-align:center;color:var(--white);font-weight:700;font-size:32px}
  .sermons-head{position:absolute;left:24px;top:141px;width:318px;height:27px;background:var(--ink);color:var(--white);
    font-weight:700;font-size:15px;line-height:27px;padding-left:6px;letter-spacing:.3px}
  .sermons{position:absolute;left:24px;top:168px;width:354px;border-collapse:collapse;border:2px solid var(--ink)}
  .sermons td{height:25.5px;border:2px solid var(--ink);color:var(--white);font-weight:700;font-size:16.5px;padding:0 9px;letter-spacing:.3px;line-height:1}
  .sermons td.date{width:118px}
  .side{position:absolute;left:405px;width:150px;color:var(--ink)}
  .side h3{font-weight:700;font-size:15.5px;line-height:1.25;letter-spacing:.4px;padding-bottom:5px;border-bottom:1px solid var(--mist);margin-bottom:9px}
  .side--features{top:137px}
  .side--about{top:265px}
  .features li{list-style:none;font-family:"Lato",sans-serif;font-size:8.6px;line-height:1.3;margin-bottom:5px;padding-left:8px;position:relative}
  .features li::before{content:"";position:absolute;left:0;top:4px;width:3px;height:3px;border-radius:50%;background:var(--ink)}
  .about p{font-family:"Lato",sans-serif;font-size:6.6px;line-height:1.38;text-align:justify;margin-bottom:3px}
  .contact{position:absolute;left:0;right:0;bottom:0;height:58px;background:var(--ink);color:var(--white);text-align:center;padding-top:10px}
  .contact p{font-size:13px;line-height:18px}
  .contact p.small{font-size:11.6px}
</style>
</head>
<body>

<section class="card card--front">
  <div class="front-photo" role="img" aria-label="Soft-focus silhouette of a family walking together through a misty meadow"></div>
  <div class="front-frame"></div>
  <div class="brand">
    <span class="brand-dot"></span>
    <span class="brand-name">Maplebrook Family Church</span>
  </div>
  <h1 class="series-title">MESSY</h1>
  <p class="series-tagline">JOINING GOD IN THE MESS</p>
  <p class="front-url">www.maplebrookchurch.ca</p>
</section>

<section class="card card--back">
  <h2 class="services-title">The time of the services</h2>
  <p class="services-time">Sundays @ 10:30</p>

  <div class="sermons-head">NAMES &amp; DATES OF THE SERMONS:</div>
  <table class="sermons">
    <tr><td class="date">April 28th</td><td>We Made This Mess</td></tr>
    <tr><td class="date">May 5th</td><td>Bless in the Mess</td></tr>
    <tr><td class="date">May 12th</td><td>Born into the Mess</td></tr>
    <tr><td class="date">May 19th</td><td>Messy Work</td></tr>
    <tr><td class="date">May 26th</td><td>Messy Church</td></tr>
    <tr><td class="date">June 2nd</td><td>Messy Hospitality</td></tr>
    <tr><td class="date">June 9th</td><td>TBD</td></tr>
    <tr><td class="date">June 16th</td><td>Messy within Boundaries</td></tr>
  </table>

  <div class="side side--features">
    <h3>OFEATURES OF THE SERVICE:</h3>
    <ul class="features">
      <li>Staffed nursery &amp; children's program every Sunday</li>
      <li>Coffee &amp; snacks</li>
      <li>Everyone welcome</li>
    </ul>
  </div>

  <div class="side side--about">
    <h3>ABOUT THE CHURCH</h3>
    <div class="about">
      <p>Maplebrook Family Church is a multicultural, multi-generational Christian community, serving Riverton and Lakeshore. We are a part of the Northern Fellowship of Churches.</p>
      <p>As Riverton grew by welcoming people from all over the world, so did Maplebrook Family Church.</p>
    </div>
  </div>

  <div class="contact">
    <p>Loaction - 1180 Birchwood Line West Riverton, ON&nbsp; L4X 2B7</p>
    <p class="small">Phone-905.555.0142 | Email-info@maplebrookchurch.ca | Website-www.maplebrookchurch.ca</p>
  </div>
</section>

</body>
</html>
```